American cannabis tech company business card design

Pavrel.com is seeking a modern, professional, and brand-aligned business card that represents our company and its core values: Mission, Story, Values, and Impact. As an innovative cannabis company, we want a business card that is not only visually appealing but also serves as a representation of who we are and what we stand for.

Project Scope: Design a double-sided business card that integrates our brand identity and core values. Incorporate our key brand elements, ensuring a sleek and contemporary aesthetic. Visually reflect our core values (Mission, Story, Values, Impact) in a way that is engaging yet professional.

Target Market(s)

Vendors, third parties,

Contact Information for Business Card

Contact details (name, title, email, phone, website, etc.)

Font styles to use
Other font styles liked:
• Caslon, Centra

Colors

Designer to choose colors to be used in the design.

Requirements
Must have
• Pavrel.com logo and branding A creative yet clean way to integrate our core values (Mission, Story, Values, Impact) Modern typography and a well-structured layout
Nice to have
• forest green, grey, white, black
Should not have
• references to marijuana, leafs, plants, or related product

```html
<!DOCTYPE html>
<html lang="en">
<head>
<meta charset="UTF-8">
<title>Pavrel Business Card</title>
<link href="https://fonts.googleapis.com/css2?family=Outfit:wght@400;600;700&display=swap" rel="stylesheet">
<style>
  :root {
    --backdrop: #979797;
    --forest-dark: #1b3420;
    --forest-mid: #2a4d2c;
    --cream: #fef5ec;
    --cream-mark: #fbe5cc;
    --ink: #1d2e1c;
    --rule: #6f6f60;
    --white: #ffffff;
    --value-tint: rgba(255,255,255,0.72);
  }
  * { margin: 0; padding: 0; box-sizing: border-box; }
  html, body {
    width: 1200px;
    height: 1000px;
    overflow: hidden;
    background: var(--backdrop);
    font-family: "Outfit", sans-serif;
  }
  .card {
    position: absolute;
    width: 694px;
    height: 400px;
    border-radius: 26px;
    overflow: hidden;
    box-shadow: 0 18px 40px rgba(0,0,0,0.28);
  }
  .card-front {
    left: 252px;
    top: 60px;
    background:
      radial-gradient(ellipse 60% 70% at 78% 60%, var(--forest-mid) 0%, rgba(42,77,44,0) 70%),
      linear-gradient(135deg, #1f3a22 0%, var(--forest-dark) 60%, #22402a 100%);
  }
  .tagline {
    position: absolute;
    left: 0;
    right: 0;
    top: 196px;
    text-align: center;
    color: var(--white);
    font-weight: 600;
    font-size: 48px;
    line-height: 1;
  }
  .core-values {
    position: absolute;
    left: 0;
    right: 0;
    top: 262px;
    text-align: center;
    color: var(--value-tint);
    font-weight: 400;
    font-size: 15px;
    letter-spacing: 3px;
    text-transform: uppercase;
  }
  .card-back {
    left: 253px;
    top: 490px;
    background: var(--cream);
    color: var(--ink);
  }
  .brand-mark {
    position: absolute;
    left: 38px;
    top: 92px;
    font-weight: 700;
    font-size: 40px;
    line-height: 1;
    color: var(--cream-mark);
    letter-spacing: 1px;
  }
  .person-name {
    position: absolute;
    left: 34px;
    top: 236px;
    font-weight: 600;
    font-size: 27px;
    line-height: 1;
  }
  .person-title {
    position: absolute;
    left: 34px;
    top: 270px;
    font-weight: 400;
    font-size: 18px;
    line-height: 1;
  }
  .divider {
    position: absolute;
    left: 34px;
    top: 302px;
    width: 620px;
    height: 2px;
    background: var(--rule);
  }
  .contact {
    position: absolute;
    left: 34px;
    top: 314px;
    font-size: 17px;
    line-height: 21px;
  }
  .website {
    position: absolute;
    right: 48px;
    top: 340px;
    font-size: 17px;
    line-height: 21px;
  }
  .website strong { font-weight: 700; }
</style>
</head>
<body>
  <section class="card card-front">
    <p class="tagline">Clarity for every need.</p>
    <p class="core-values">Mission · Story · Values · Impact</p>
  </section>

  <section class="card card-back">
    <div class="brand-mark">PAVREL</div>
    <h1 class="person-name">Marcus Hale</h1>
    <p class="person-title">Co-Founder &amp; CEO</p>
    <div class="divider"></div>
    <p class="contact">405-555-0148<br>name@pavrel.com</p>
    <p class="website"><strong>pavrel</strong>.com</p>
  </section>
</body>
</html>
```